Business Card & Letterhead Design

We a financial advice company based in Australia. We provide advice to wealthy farmers.

We are changing our business name FROM Brightvale Financial TO Tallowmere Wealth and we need a new letterhead and double sided business card design

Attached is designs from our previous branding (Brightvale Financial) as it includes all the details we require on the new Tallowmere Wealth business cards and letterhead.

Need extra days to review

```html
<!DOCTYPE html>
<html lang="en">
<head>
<meta charset="utf-8">
<title>Tallowmere Wealth Letterhead</title>
<link rel="stylesheet" href="https://fonts.googleapis.com/css2?family=Open+Sans:wght@400;600;700&display=swap">
<style>
  :root {
    --backdrop: #e4e4e4;
    --paper: #ffffff;
    --ink: #3a3a3a;
    --ink-soft: #5a5a5a;
    --brand: #2f2f2f;
    --footer-band: #4a4a4a;
    --footer-text: #ffffff;
    --ring: #ececec;
  }
  * { box-sizing: border-box; margin: 0; padding: 0; }
  html, body {
    width: 1040px; height: 1200px; overflow: hidden;
    background: var(--backdrop);
    font-family: "Open Sans", Arial, sans-serif;
    color: var(--ink);
  }
  .letterhead {
    position: absolute; left: 54px; top: 1px;
    width: 932px; height: 1198px;
    background: var(--paper);
    overflow: hidden;
  }
  .backdrop-ring {
    position: absolute; left: 247px; top: 451px;
    width: 436px; height: 436px;
  }
  .brand {
    position: absolute; left: 87px; top: 27px;
    display: flex; flex-direction: column; align-items: center; width: 240px;
  }
  .brand-circle {
    width: 62px; height: 62px; border: 2px solid var(--brand); border-radius: 50%;
  }
  .brand-name {
    margin-top: 8px; font-size: 21px; font-weight: 400; letter-spacing: 1.5px;
    color: var(--brand); text-transform: uppercase; white-space: nowrap;
  }
  .company-details {
    position: absolute; right: 98px; top: 36px;
    text-align: right; font-size: 15px; line-height: 21.8px; color: #222;
    font-style: normal;
  }
  .company-details .contact { display: flex; justify-content: flex-end; align-items: center; gap: 3px; }
  .company-details svg { width: 11px; height: 11px; fill: #222; }
  .issue-date { position: absolute; left: 87px; top: 272px; font-size: 14px; color: var(--ink-soft); }
  .recipient {
    position: absolute; left: 87px; top: 308px;
    font-size: 14px; line-height: 18px; color: var(--ink-soft);
  }
  .letter-body {
    position: absolute; left: 87px; top: 413px; width: 752px;
    font-size: 14px; line-height: 27px; color: var(--ink-soft);
    text-align: justify; hyphens: auto;
  }
  .letter-body p { margin-bottom: 27px; }
  .letter-body .salutation { margin-bottom: 26px; }
  .sign-off { position: absolute; left: 87px; top: 870px; font-size: 14px; color: var(--ink-soft); }
  .signatory { position: absolute; left: 87px; top: 948px; }
  .signatory-name { font-size: 18px; color: var(--ink); }
  .signatory-title { font-size: 14px; color: var(--ink-soft); margin-top: 3px; }
  .footer-band {
    position: absolute; left: 0; bottom: 0; width: 100%; height: 103px;
    background: var(--footer-band); color: var(--footer-text);
  }
  .footer-motto {
    position: absolute; left: 80px; top: 38px; width: 222px;
    text-align: center; font-size: 14px; font-weight: 700; line-height: 27px;
    white-space: nowrap;
  }
  .footer-licensee {
    position: absolute; right: 98px; top: 12px;
    text-align: right; font-size: 15px; font-weight: 600; line-height: 22px;
    white-space: nowrap;
  }
  .footer-licensee .address { margin-top: 5px; }
</style>
</head>
<body>
<main class="letterhead">
  <svg class="backdrop-ring" viewBox="0 0 436 436" aria-hidden="true">
    <circle cx="218" cy="218" r="212" fill="none" stroke="var(--ring)" stroke-width="10"/>
  </svg>

  <header class="brand">
    <div class="brand-circle"></div>
    <div class="brand-name">Tallowmere Wealth</div>
  </header>

  <address class="company-details">
    <div>Kestrel Ridge Holdings Pty Ltd</div>
    <div>ATF The Marlow Investment</div>
    <div>Trust T/AS Brightvale Financial</div>
    <div>ABN: 58 302 119 647</div>
    <div>Corporate Authorised</div>
    <div>Representative Of Summit</div>
    <div>Advisory Planning Limited</div>
    <div>Suite 4C, 18 Farrow St</div>
    <div>Riverbend QLD 4170</div>
    <div>PO Box 5312</div>
    <div>Eastvale QLD 4172</div>
    <div class="contact">(07) 3000 1234
      <svg viewBox="0 0 12 12" aria-label="phone"><path d="M1 4c0-2 2-3 5-3s5 1 5 3l-2 1-1-1.5H4L3 5zM3 6h6l1 5H2z"/></svg></div>
    <div class="contact">(07) 3000 5678
      <svg viewBox="0 0 12 12" aria-label="fax"><path d="M3 1h6v3H3zM1 5h10v5H9V8H3v2H1zM3.5 9h5v2.5h-5z"/></svg></div>
    <div class="contact">sam@brightvalefinancial.com.au
      <svg viewBox="0 0 12 12" aria-label="email"><path d="M1 2.5h10v7H1zM1.5 3l4.5 3.5L10.5 3" stroke="#fff" stroke-width=".8"/></svg></div>
    <div class="contact">www.brightvalefinancial.com.au
      <svg viewBox="0 0 12 12" aria-label="website"><circle cx="6" cy="6" r="5"/><path d="M1 6h10M6 1c-2.5 3-2.5 7 0 10M6 1c2.5 3 2.5 7 0 10" stroke="#fff" stroke-width=".7" fill="none"/></svg></div>
  </address>

  <div class="issue-date">Issuing Date: May 5, 2018</div>
  <div class="recipient">
    <div>Name Of Employee Mr. XYZABC</div>
    <div>Address of Employee</div>
    <div>Address Line 2 etc..</div>
  </div>

  <section class="letter-body">
    <p class="salutation">Dear Mr.XYZABC</p>
    <p>Lorem Ipsum has been the industry's standard dummy text ever since the 1500s, when an unknown printer took a galley of type and scrambled it to make a type specimen book. It has survived not only five centuries, but also the leap into electronic typesetting, remaining essentially unchanged. It was popularised in the 1960s with the release of Letraset sheets containing Lorem Ipsum passages, and more recently with desktop publishing software like Aldus PageMaker including versions of Lorem Ipsum.</p>
    <p>Lorem Ipsum is simply dummy text of the printing and typesetting industry. Lorem Ipsum has been the industry's standard dummy text ever since the 1500s, when an unknown printer took a galley of type and scrambled it to make a type specimen book.</p>
    <p>It has survived not only five centuries, but also the leap into electronic typesetting, remaining essentially unchanged. It was popularised in the 1960s with the release of Letraset sheets containing Lorem IpsumIpsum passages.</p>
  </section>

  <div class="sign-off">Yours Sincerely</div>
  <div class="signatory">
    <div class="signatory-name">Daniel Hartley</div>
    <div class="signatory-title">Managing Director</div>
  </div>

  <footer class="footer-band">
    <div class="footer-motto">
      <div>‘STEADY GROWTH, CLEAR PLANS’</div>
      <div>TRUSTED ACROSS THE LAND</div>
    </div>
    <div class="footer-licensee">
      <div>Summit Advisory Planning Limited &nbsp;| ABN 41 009 553 218</div>
      <div>Australian &nbsp;Financial Services License | License Number 318842</div>
      <div class="address">Principle Address: 120 Harbour Rd. PO Box 4410 Portside VIC 3010</div>
    </div>
  </footer>
</main>
</body>
</html>
```